Residential Remodeling Contractor needs updated business card

I need a new design for my business card.
Name of the company is Ridgefell Construction. I need a card that commands presence, strength, integrity. I have been in business for 28 years. I am a Residential Remodeling Contractor that covers all aspects of a residential remodel and build.

```html
<!DOCTYPE html>
<html lang="en">
<head>
<meta charset="utf-8">
<title>Ridgefell Construction — Business Card</title>
<link href="https://fonts.googleapis.com/css2?family=Open+Sans:wght@400;700&display=swap" rel="stylesheet">
<style>
  :root {
    --backdrop: #222222;
    --card-blue: #203d7e;
    --card-edge: #172d61;
    --ink-white: #ffffff;
    --ink-soft: #dfe5f3;
    --rule: rgba(255,255,255,0.7);
    --mark-shade: #3a5aa6;
  }
  * { margin: 0; padding: 0; box-sizing: border-box; }
  html, body {
    width: 1200px; height: 780px; overflow: hidden;
    background: var(--backdrop);
    font-family: "Open Sans", Arial, sans-serif;
  }
  .canvas {
    width: 1200px; height: 780px;
    display: flex; align-items: center; justify-content: center; gap: 60px;
  }
  .card {
    position: relative;
    width: 525px; height: 300px;
    background: var(--card-blue);
    box-shadow: 0 3px 0 var(--card-edge), 0 6px 0 var(--card-edge), 0 18px 30px rgba(0,0,0,0.5);
    color: var(--ink-white);
    overflow: hidden;
  }
  /* front */
  .card-front .brand {
    position: absolute; left: 40px; top: 70px;
    display: flex; align-items: center; gap: 12px;
  }
  .brand-square {
    width: 18px; height: 18px; background: var(--ink-white);
  }
  .brand-name {
    font-size: 22px; font-weight: 700; letter-spacing: 1.5px;
    text-transform: uppercase; line-height: 1.15;
    color: var(--ink-white);
  }
  .divider {
    position: absolute; left: 262px; top: 60px;
    width: 1px; height: 150px; background: var(--rule);
    transform: rotate(12deg);
  }
  .person {
    position: absolute; left: 300px; top: 62px;
  }
  .person-name { font-size: 27px; font-weight: 700; line-height: 1.1; }
  .person-title { font-size: 15px; color: var(--ink-soft); margin-top: 2px; }
  .contacts { list-style: none; margin-top: 18px; }
  .contacts li {
    display: flex; align-items: center; gap: 8px;
    font-size: 13px; line-height: 1.7;
  }
  .contacts svg { width: 13px; height: 13px; fill: var(--ink-white); flex: none; }
  .address {
    position: absolute; left: 40px; bottom: 36px;
    font-size: 13.5px; color: var(--ink-white);
  }
  /* back */
  .card-back .brand {
    position: absolute; left: 0; right: 0; top: 0; bottom: 0;
    display: flex; align-items: center; justify-content: center; gap: 16px;
  }
  .card-back .brand-square { width: 26px; height: 26px; background: var(--mark-shade); }
  .card-back .brand-name {
    font-size: 32px; letter-spacing: 2.5px; color: var(--mark-shade);
  }
</style>
</head>
<body>
<main class="canvas">
  <section class="card card-front" aria-label="Business card front">
    <div class="brand">
      <span class="brand-square"></span>
      <span class="brand-name">Ridgefell<br>Construction</span>
    </div>
    <span class="divider"></span>
    <div class="person">
      <p class="person-name">Daniel Hargrove</p>
      <p class="person-title">Managing Director</p>
      <ul class="contacts">
        <li>
          <svg viewBox="0 0 24 24" aria-hidden="true"><path d="M6.6 10.8a15.1 15.1 0 0 0 6.6 6.6l2.2-2.2a1 1 0 0 1 1-.25 11.4 11.4 0 0 0 3.6.57 1 1 0 0 1 1 1V20a1 1 0 0 1-1 1A17 17 0 0 1 3 4a1 1 0 0 1 1-1h3.5a1 1 0 0 1 1 1c0 1.25.2 2.45.57 3.57a1 1 0 0 1-.25 1z"/></svg>
          (555) 014-2290
        </li>
        <li>
          <svg viewBox="0 0 24 24" aria-hidden="true"><path d="M2 5h20v14H2zm2 2v.5l8 5 8-5V7zm0 2.8V17h16V9.8l-8 5z"/></svg>
          info@ridgefellbuild.com
        </li>
        <li>
          <svg viewBox="0 0 24 24" aria-hidden="true"><path d="M12 2a10 10 0 1 0 0 20 10 10 0 0 0 0-20zm0 2c.9 0 2.3 2 2.8 7H9.2C9.7 6 11.1 4 12 4zm-3 .6A14 14 0 0 0 7.2 11H4.1A8 8 0 0 1 9 4.6zm6 0A8 8 0 0 1 19.9 11h-3.1A14 14 0 0 0 15 4.6zM4.1 13h3.1A14 14 0 0 0 9 19.4 8 8 0 0 1 4.1 13zm5.1 0h5.6c-.5 5-1.9 7-2.8 7s-2.3-2-2.8-7zm7.6 0h3.1A8 8 0 0 1 15 19.4a14 14 0 0 0 1.8-6.4z"/></svg>
          www.ridgefellbuild.com
        </li>
      </ul>
    </div>
    <p class="address">1480 Alder Crest Rd. Suite 310 Ashford, TX 75001</p>
  </section>

  <section class="card card-back" aria-label="Business card back">
    <div class="brand">
      <span class="brand-square"></span>
      <span class="brand-name">Ridgefell<br>Construction</span>
    </div>
  </section>
</main>
</body>
</html>
```